Business Card for Coastal Tundrabridge Advisory

We need a business card for Coastal Tundrabridge Advisory. The company website address is provided below. The company logo is attached. We provide specialized permafrost services to the mining, transportation, and oil & gas industries. The card should be prepared for:
Matthias Korhonen, PhD.
Coastal Tundrabridge Advisory
PO Box 418259
Quillwater, Alaska 99642
Direct: +1-907-555-0143
Email: mkorhonen@tundrabridgeadvisory.example
Website: www.coastaltundrabridgeadvisory.example

```html
<!DOCTYPE html>
<html lang="en">
<head>
<meta charset="utf-8">
<title>Coastal Tundrabridge Advisory — Business Card</title>
<link rel="stylesheet" href="https://fonts.googleapis.com/css2?family=Montserrat:wght@400;700&display=swap">
<style>
  :root {
    --backdrop: #d6d6d6;
    --card: #f2f2f2;
    --ink: #0d0d0d;
    --edge: #1a1a1a;
  }
  * { margin: 0; padding: 0; box-sizing: border-box; }
  html, body { width: 1200px; height: 1051px; overflow: hidden; }
  body {
    background: var(--backdrop);
    font-family: "Montserrat", sans-serif;
    color: var(--ink);
    display: flex;
    flex-direction: column;
    align-items: center;
    justify-content: center;
    gap: 50px;
  }
  .card {
    width: 700px;
    height: 400px;
    background: var(--card);
    border-bottom: 4px solid var(--edge);
    box-shadow: 0 14px 30px rgba(0,0,0,0.18);
    display: flex;
    flex-direction: column;
    align-items: center;
    justify-content: center;
    text-align: center;
    padding: 0 40px;
  }
  .brand {
    display: inline-flex;
    align-items: center;
    justify-content: center;
    gap: 14px;
    font-weight: 700;
    text-transform: uppercase;
    letter-spacing: 0.04em;
    white-space: nowrap;
  }
  .brand-dot {
    width: 18px; height: 18px;
    border-radius: 50%;
    background: var(--ink);
    flex: none;
  }
  .card-front .brand { font-size: 26px; }
  .card-back .brand { font-size: 21px; margin-bottom: 16px; }
  .card-back .brand-dot { width: 12px; height: 12px; }
  .person-name { font-weight: 700; font-size: 22px; }
  .person-company { font-size: 15px; margin-bottom: 12px; }
  .icon-row { display: flex; gap: 8px; justify-content: center; margin: 6px 0; }
  .icon {
    width: 22px; height: 22px;
    border-radius: 50%;
    background: var(--ink);
    display: flex; align-items: center; justify-content: center;
  }
  .icon svg { width: 13px; height: 13px; }
  .address-line, .contact-line { font-size: 15px; line-height: 1.4; }
  .address { margin-bottom: 10px; }
</style>
</head>
<body>
  <section class="card card-front">
    <div class="brand"><span class="brand-dot"></span><span class="brand-name">Coastal Tundrabridge Advisory</span></div>
  </section>

  <section class="card card-back">
    <div class="brand"><span class="brand-dot"></span><span class="brand-name">Coastal Tundrabridge Advisory</span></div>
    <p class="person-name">Matthias Korhonen, PhD</p>
    <p class="person-company">Coastal Tundrabridge Advisory</p>

    <div class="icon-row">
      <span class="icon">
        <svg viewBox="0 0 24 24"><path fill="#fff" d="M12 2a7 7 0 0 0-7 7c0 5 7 13 7 13s7-8 7-13a7 7 0 0 0-7-7zm0 9.5A2.5 2.5 0 1 1 12 6.5a2.5 2.5 0 0 1 0 5z"/></svg>
      </span>
    </div>
    <div class="address">
      <p class="address-line">Coastal Tundrabridge Advisory</p>
      <p class="address-line">PO Box 418259</p>
    </div>

    <div class="icon-row">
      <span class="icon">
        <svg viewBox="0 0 24 24"><path fill="#fff" d="M6.6 10.8a15 15 0 0 0 6.6 6.6l2.2-2.2a1 1 0 0 1 1-.25 11.4 11.4 0 0 0 3.6.57 1 1 0 0 1 1 1V20a1 1 0 0 1-1 1A17 17 0 0 1 3 4a1 1 0 0 1 1-1h3.5a1 1 0 0 1 1 1c0 1.25.2 2.45.57 3.57a1 1 0 0 1-.25 1z"/></svg>
      </span>
      <span class="icon">
        <svg viewBox="0 0 24 24"><path fill="#fff" d="M3 5h18v14H3zm2 2v.5l7 4.5 7-4.5V7l-7 4.5z"/></svg>
      </span>
      <span class="icon">
        <svg viewBox="0 0 24 24" fill="none" stroke="#fff" stroke-width="2"><circle cx="12" cy="12" r="9"/><path d="M3 12h18M12 3c3 3 3 15 0 18M12 3c-3 3-3 15 0 18"/></svg>
      </span>
    </div>
    <p class="contact-line">mkorhonen@tundrabridgeadvisory.example</p>
    <p class="contact-line">+1-907-555-0143</p>
    <p class="contact-line">www.coastaltundrabridgeadvisory.example</p>
  </section>
</body>
</html>
```